Stylish High End Wedding Videography/Films Website (BMRT)

We need a modern and high-end website look for our wedding video and films business. We films weddings all over the United Kingdom and at European destinations so need something to reflect our work. The website should be visually stunning with images and videos being the focal point as this is what our services are;

I have uploads of some items I like and the features the site needs to have. These have been taken from other websites using standout features.

We need the following pages;

1 - Homepage
2 - Films Index Page
3 - Individual Films Page
4 - Prices / Collection Page
5 - Reviews
6 - Options
7 - About
8 - Contact
9 - Blog Index
10 - Blog Page

All pages must be consistent so have a similar style.

Pages on menu:
Films
Prices
Reviews
Options
About
Contact

We require a responsive look too. Over 90% of our visitors access the website via their mobile devices.

Please use the colours from our logo to incorporate into the website.

Target Market(s)

Wedding Couples

Industry/Entity Type

Wedding Photography

Number of Pages Required

5+ page

Font styles to use
Sans Serif
Script

Requirements
Must have
• The logo must be in the centre of the menu at the top.

Social icons at the bottom of the page.

Use only two fonts including Lore which is supplied
Nice to have
• Different video for each page on the top header. This will play behind the menu.

```html
<!DOCTYPE html>
<html lang="en">
<head>
<meta charset="utf-8">
<title>BMRT Wedding Films</title>
<link href="https://fonts.googleapis.com/css2?family=Montserrat:wght@400;500;600;700&display=swap" rel="stylesheet">
<style>
:root{
  --gold:#a68b55;
  --gold-band:#a38a57;
  --ink:#2d2627;
  --muted:#8a8585;
  --quote:#6b6465;
  --soft:#f5f4f4;
  --footer:#2a2526;
  --line:#e2dfdf;
  --white:#ffffff;
}
*{margin:0;padding:0;box-sizing:border-box}
html,body{width:1200px;height:4016px;overflow:hidden}
body{position:relative;background:var(--white);font-family:"Montserrat",sans-serif;color:var(--ink)}
.abs{position:absolute}
.photo{position:absolute}

/* hero */
.hero{left:0;top:0;width:1200px;height:650px;background:
  radial-gradient(ellipse at 60% 30%,rgba(200,200,190,.35),transparent 40%),
  linear-gradient(180deg,#1b1a16 0%,#3a3a2c 30%,#4d4c45 60%,#2c2b29 100%)}
.nav{top:101px;display:flex;gap:26px;align-items:center;font-size:11px;letter-spacing:2.4px;font-weight:500;color:var(--white)}
.nav .dot{width:3px;height:3px;border-radius:50%;background:var(--white)}
.nav .active{color:var(--gold)}
.nav-left{left:175px}
.nav-right{left:764px}
.brand{left:500px;top:88px;width:200px;text-align:center;color:var(--white);font-weight:500}
.brand .name{font-size:19px;letter-spacing:6px}
.brand .sub{font-size:9px;letter-spacing:4px;margin-top:1px}
.counter{left:562px;top:583px;color:var(--white);font-size:13px;display:flex;gap:14px;align-items:center}
.counter .cur{font-weight:600}
.counter .slash{width:1px;height:18px;background:rgba(255,255,255,.7);transform:rotate(30deg)}

/* headings */
.section-title{width:1200px;left:0;text-align:center;font-size:26px;font-weight:600;color:var(--ink)}

/* service cards */
.card{top:807px;width:283px;height:333px;border-left:1px solid var(--line)}
.card .pic{position:absolute;left:0;top:0;width:283px;height:190px}
.card h3{position:absolute;left:23px;top:212px;font-size:14.5px;font-weight:600}
.card p{position:absolute;left:23px;top:234px;width:250px;font-size:10.5px;line-height:20px;color:var(--muted)}
.more{position:absolute;left:0;top:313px;height:16px;border-left:2px solid var(--gold);padding-left:21px;font-size:9px;letter-spacing:2px;font-weight:600;line-height:16px}

/* about */
.about-bg{left:458px;top:1242px;width:742px;height:611px;background:linear-gradient(180deg,#f6f6f6 0%,#efefef 60%,#e4e4e2 100%)}
.about-photo{left:76px;top:1320px;width:524px;height:458px;background:linear-gradient(180deg,#dfe1e1 0%,#c9cccb 45%,#7f8a55 75%,#55632f 100%)}
.about-lead{left:676px;top:1403px;width:370px;font-size:15.5px;line-height:23px}
.about-lead em{font-style:normal;color:var(--gold)}
.about-text{left:676px;width:372px;font-size:10.5px;line-height:20px;color:var(--muted)}
.link-label{height:16px;border-left:2px solid var(--gold);padding-left:24px;font-size:9px;letter-spacing:2px;font-weight:600;line-height:16px}

/* showcase */
.video{left:268px;top:2010px;width:665px;height:458px;background:linear-gradient(135deg,#2f3a26 0%,#5a5048 40%,#2c2a2a 70%,#3b4730 100%)}
.play{left:562px;top:2201px;width:76px;height:76px}
.vid-num{top:2230px;color:var(--white);font-size:14px;font-weight:600}
.side-arrow{top:2228px}
.vert{left:176px;top:2470px;transform-origin:left top;transform:rotate(-90deg);white-space:nowrap}
.vert .num{color:var(--gold);font-size:15px;font-weight:600;margin-right:24px}
.vert .couple{font-size:15px;font-weight:600}
.vert .venue{position:absolute;left:120px;top:26px;font-size:11px;color:var(--muted)}

/* testimonial */
.testimonial{left:0;top:2623px;width:1200px;height:374px;background:var(--soft)}
.quote{left:0;top:2712px;width:1200px;text-align:center;font-size:15.5px;line-height:31px;color:var(--quote)}
.quote .mark{color:var(--gold);font-size:11px;vertical-align:top}
.avatar{left:570px;top:2837px;width:60px;height:60px;border-radius:50%;background:radial-gradient(circle,#c9b8a3,#6a5a4e)}
.person{left:0;top:2910px;width:1200px;text-align:center;font-size:10.5px;letter-spacing:1.6px;font-weight:600}

/* photography */
.gallery-item{top:3154px;width:283px}
.gallery-item .pic{width:283px;height:282px}
.gallery-item h4{margin-top:32px;font-size:14.5px;font-weight:500}
.gallery-item p{margin-top:4px;font-size:10.5px;line-height:20px;color:var(--muted);width:220px}
.gallery-item.featured h4{color:var(--gold)}

/* cta */
.cta{left:0;top:3610px;width:1200px;height:151px;background:var(--gold-band)}
.cta h2{position:absolute;left:293px;top:55px;font-size:27px;font-weight:600;color:var(--ink)}
.cta .btn{position:absolute;left:689px;top:52px;width:192px;height:48px;background:var(--footer);color:#c9a867;font-size:11px;font-weight:600;letter-spacing:.6px;display:flex;align-items:center;justify-content:center}

/* footer */
.footer{left:0;top:3761px;width:1200px;height:255px;background:var(--footer)}
.footer-brand{left:153px;top:3838px;font-size:34px;font-weight:600;letter-spacing:5px;color:var(--gold)}
.footer-col{color:var(--white)}
.f-label{font-size:10.5px;letter-spacing:2px;font-weight:600;color:var(--white)}
.f-main{font-size:15px;font-weight:500;margin-top:12px;color:var(--white)}
.f-main span{color:var(--gold)}
.f-sub{font-size:11px;color:#a9a3a3;margin-top:6px}
.badge{left:986px;top:3829px;width:56px;height:56px;border-radius:50%;background:#f2df86;border:2px solid #d9c15f}
.divider{left:76px;top:3953px;width:1047px;height:1px;background:#443e3f}
.copyright{left:153px;top:3977px;font-size:10.5px;color:#c3bdbd}
.social{top:3969px;width:28px;height:28px;border-radius:50%;background:#4a4445;display:flex;align-items:center;justify-content:center}
</style>
</head>
<body>

<!-- hero -->
<div class="abs hero photo" role="img" aria-label="Bride and groom embracing on a rocky shore in front of a waterfall"></div>
<nav class="abs nav nav-left"><span class="active">FILMS</span><span class="dot"></span><span>PRICES</span><span class="dot"></span><span>REVIEWS</span></nav>
<div class="abs brand"><div class="name">BMRT</div><div class="sub">WEDDING FILMS</div></div>
<nav class="abs nav nav-right"><span>OPTIONS</span><span class="dot"></span><span>ABOUT</span><span class="dot"></span><span>CONTACT</span></nav>
<svg class="abs" style="left:341px;top:584px" width="22" height="14" viewBox="0 0 22 14"><path d="M21 7H2M7 2L2 7l5 5" fill="none" stroke="#fff" stroke-width="1.6"/></svg>
<div class="abs counter"><span class="cur">02</span><span class="slash"></span><span>06</span></div>
<svg class="abs" style="left:838px;top:584px" width="22" height="14" viewBox="0 0 22 14"><path d="M1 7h19M15 2l5 5-5 5" fill="none" stroke="#fff" stroke-width="1.6"/></svg>

<!-- services -->
<h2 class="abs section-title" style="top:735px">What Can We Do</h2>
<div class="abs card" style="left:153px">
  <div class="pic" role="img" aria-label="Couple laughing under falling confetti" style="background:linear-gradient(135deg,#d9cfc2,#8a6a4a 55%,#5b4535)"></div>
  <h3>Shooting &amp; Editing</h3>
  <p>Ut enim ad minim veniam, nostrud exercita-tion ullamco laboris nisi ut aliquip ex ea commodo consequat ...</p>
  <div class="more">MORE</div>
</div>
<div class="abs card" style="left:458px">
  <div class="pic" role="img" aria-label="Engagement ring hanging from a blossom branch" style="background:linear-gradient(135deg,#5a5230,#8c7c5a 50%,#6b6040)"></div>
  <h3>Creative Conceptions</h3>
  <p>Ut enim ad minim veniam, nostrud exercita-tion ullamco laboris nisi ut aliquip ex ea commodo consequat ...</p>
  <div class="more">MORE</div>
</div>
<div class="abs card" style="left:764px">
  <div class="pic" role="img" aria-label="Couple embracing by the sea cliffs" style="background:linear-gradient(135deg,#6f7a84,#4a5056 50%,#a69a8c)"></div>
  <h3>Unique Photography</h3>
  <p>Ut enim ad minim veniam, nostrud exercita-tion ullamco laboris nisi ut aliquip ex ea commodo consequat ...</p>
  <div class="more">MORE</div>
</div>

<!-- about -->
<div class="abs about-bg photo" role="img" aria-label="Faded image of a couple in a grassy field"></div>
<div class="abs about-photo photo" role="img" aria-label="Videographer filming with a stabilizer in a meadow"></div>
<p class="abs about-lead">Ut enim ad minim veniam, <em>quis nostrud exerci-tation ullamco laboris</em> nisi ut aliquip ex ea com-modo consequat.</p>
<p class="abs about-text" style="top:1492px">Nemo enim ipsam voluptatem quia voluptas sit aspernatur aut odit aut fugit, sed quia consequuntur magni dolores eos qui ra-tione voluptatem sequi nesciunt.</p>
<p class="abs about-text" style="top:1571px">Neque porro quisquam est, qui dolorem ipsum quia dolor sit amet, consectetur, adipisci velit, sed quia non numquam eius modi tempora incidunt ut labore et dolore magnam</p>
<div class="abs link-label" style="left:679px;top:1672px">ABOUT US</div>

<!-- showcase -->
<h2 class="abs section-title" style="top:1937px">Wedding Showcase</h2>
<div class="abs video photo" role="img" aria-label="Bride and groom walking through a shower of petals"></div>
<svg class="abs play" viewBox="0 0 76 76"><circle cx="38" cy="38" r="38" fill="rgba(255,255,255,.22)"/><path d="M31 26l18 12-18 12z" fill="none" stroke="#fff" stroke-width="2"/></svg>
<div class="abs vid-num" style="left:342px">02</div>
<div class="abs vid-num" style="left:838px">06</div>
<svg class="abs side-arrow" style="left:105px" width="18" height="12" viewBox="0 0 18 12"><path d="M17 6H2M6 2L2 6l4 4" fill="none" stroke="#bdb8b8" stroke-width="1.2"/></svg>
<svg class="abs side-arrow" style="left:1077px" width="18" height="12" viewBox="0 0 18 12"><path d="M1 6h15M12 2l4 4-4 4" fill="none" stroke="#bdb8b8" stroke-width="1.2"/></svg>
<div class="abs vert"><span class="num">02.</span><span class="couple">Ella &amp; Tom</span><span class="venue">Ashford Hall, Westmoor</span></div>
<div class="abs link-label" style="left:519px;top:2513px">VIEW ALL SHOWCASE</div>

<!-- testimonial -->
<div class="abs testimonial"></div>
<p class="abs quote"><span class="mark">&#8220;</span> Sed ut perspiciatis unde omnis iste natus error sit voluptatem accusantium<br>doloremque laudantium, totam rem aperiam, eaque ipsa quae ab illo inventore veritatis<br>et quasi architecto beatae vitae dicta sunt explicabo <span class="mark">&#8221;</span></p>
<svg class="abs" style="left:458px;top:2861px" width="18" height="12" viewBox="0 0 18 12"><path d="M17 6H2M6 2L2 6l4 4" fill="none" stroke="#c9c4c4" stroke-width="1.2"/></svg>
<div class="abs avatar photo" role="img" aria-label="Portrait of the reviewing couple"></div>
<svg class="abs" style="left:725px;top:2861px" width="18" height="12" viewBox="0 0 18 12"><path d="M1 6h15M12 2l4 4-4 4" fill="none" stroke="#c9c4c4" stroke-width="1.2"/></svg>
<div class="abs person">LENA MARSH</div>

<!-- photography -->
<h2 class="abs section-title" style="top:3081px">Photography</h2>
<svg class="abs" style="left:105px;top:3290px" width="18" height="12" viewBox="0 0 18 12"><path d="M17 6H2M6 2L2 6l4 4" fill="none" stroke="#c9c4c4" stroke-width="1.2"/></svg>
<svg class="abs" style="left:1077px;top:3290px" width="18" height="12" viewBox="0 0 18 12"><path d="M1 6h15M12 2l4 4-4 4" fill="none" stroke="#c9c4c4" stroke-width="1.2"/></svg>
<div class="abs gallery-item featured" style="left:153px">
  <div class="pic" role="img" aria-label="Smiling bride with groom among trees" style="background:linear-gradient(135deg,#6d7a4c,#c8b9a8 50%,#4f5a3c)"></div>
  <h4>Cat &amp; Jeff</h4>
  <p>Lorem Ipsum is simply dummy text printing and typesettin</p>
</div>
<div class="abs gallery-item" style="left:458px">
  <div class="pic" role="img" aria-label="Black and white photo of a couple walking through smoke" style="background:linear-gradient(135deg,#bdbdbd,#6e6e6e 55%,#2e2e2e)"></div>
  <h4>Amanda &amp; Smith</h4>
  <p>Lorem Ipsum is simply dummy text printing and typesettin</p>
</div>
<div class="abs gallery-item" style="left:764px">
  <div class="pic" role="img" aria-label="Couple embracing in a hillside meadow" style="background:linear-gradient(135deg,#9fb0b0,#b8a88a 50%,#6a7548)"></div>
  <h4>Cat &amp; Jeff</h4>
  <p>Lorem Ipsum is simply dummy text printing and typesettin</p>
</div>

<!-- call to action -->
<section class="abs cta">
  <h2>Start your project with us</h2>
  <div class="btn">Get Started Now!</div>
</section>

<!-- footer -->
<footer class="abs footer"></footer>
<div class="abs footer-brand">BMRT</div>
<div class="abs footer-col" style="left:344px;top:3826px">
  <div class="f-label">CONTACT US</div>
  <div class="f-main">Call Us. <span>+44 7000 318 204</span></div>
  <div class="f-sub">e. films@bmrtfilms.example</div>
</div>
<div class="abs footer-col" style="left:676px;top:3826px">
  <div class="f-label">GET IN TOUCH</div>
  <div class="f-main">NE4 2QT Halden</div>
  <div class="f-sub">Fernvale Green United Kingdom</div>
</div>
<div class="abs badge"></div>
<svg class="abs" style="left:1153px;top:3814px" width="16" height="22" viewBox="0 0 16 22"><path d="M8 21V2M2 8l6-6 6 6" fill="none" stroke="#a68b55" stroke-width="1.5"/></svg>
<div class="abs divider"></div>
<div class="abs copyright">2020 &copy; BMRT Wedding Films. All Rights Reserved.</div>
<div class="abs social" style="left:941px" aria-label="Social link"><svg width="10" height="10" viewBox="0 0 10 10"><circle cx="5" cy="5" r="2.5" fill="#fff"/></svg></div>
<div class="abs social" style="left:980px" aria-label="Social link"><svg width="10" height="10" viewBox="0 0 10 10"><rect x="1.5" y="1.5" width="7" height="7" rx="1.5" fill="none" stroke="#fff" stroke-width="1.3"/></svg></div>
<div class="abs social" style="left:1018px" aria-label="Social link"><svg width="10" height="10" viewBox="0 0 10 10"><path d="M3 2l5 3-5 3z" fill="#fff"/></svg></div>

</body>
</html>
```